Coastal Learner Bureau business cards

Australian company about to start offering its services. We recruit international students to come to study English, vocational education and postgraduate courses in Australia. We help them find the institution and select the right city they want to come to Australia. We are a young, online oriented and supportive agency. Our clients are between 18 and 35 years old, mainly University students, young professionals or people with work experience. We provide much more information that any other agency offer. We administrate a Facebook group with more than 11.000 members that daily ask questions about general information when coming to Australia, while they are here and even after they leave the country

Target Market(s)

International students from South America, Central America and Europe

Industry/Entity Type

Student

Contact Information for Business Card

Tomas Bilbrea
Managing Director
tomas@kelvarin.com.au
www.kelvoria.com.au
+61 491058264
Melbourne, Australia

Font styles to use
Serif
Sans Serif

Colors

Designer to choose colors to be used in the design.

Requirements
Must have
• Horizontal design
• Standard business card size and shape. If font uses green or yellow colours, they will have to match the ones from the logo
Nice to have
• UPDATE: Use the contents of the green image to design one of the card sides. Use our logo in the background of that side as watermark.
• Passport image, or immigration stamps. A picture of the Yarra River (from Melbourne) would be cool as well.
Should not have
• Non-standard business card size and shape
• Not black as the background colour of any sides as we are not a VIP agency or a hight class service. We are orientes to young people and they like colours, pictures, something attractive.
• Vertical design
• NO YELLOW or BLACK AS THE BACKGROUND COLOUR OF ANY SIDE OF THE BIZ CARD

```html
<!DOCTYPE html>
<html lang="en">
<head>
<meta charset="utf-8">
<title>Coastal Learner Bureau – Business Cards</title>
<link href="https://fonts.googleapis.com/css2?family=Comic+Neue:wght@700&family=Open+Sans:ital,wght@0,400;1,700&display=swap" rel="stylesheet">
<style>
  :root {
    --bg: #e9e6e1;
    --card-white: #f7f7f7;
    --brand-green: #16724a;
    --brand-yellow: #e8c012;
    --ink-grey: #555555;
    --divider: #c9c9c9;
    --sky-top: #5a8fc9;
    --sky-mid: #c9d6e3;
    --water: #3b5f86;
    --white: #ffffff;
  }
  * { margin: 0; padding: 0; box-sizing: border-box; }
  html, body { width: 1200px; height: 960px; overflow: hidden; }
  body { background: var(--bg); position: relative; font-family: "Open Sans", sans-serif; }

  .card {
    position: absolute;
    width: 600px;
    height: 344px;
    border-radius: 16px;
    overflow: hidden;
    box-shadow: 0 3px 8px rgba(0,0,0,0.25);
  }
  .card--front { left: 302px; top: 128px; background: var(--card-white); }
  .card--back { left: 299px; top: 488px; }

  /* front */
  .brand-name {
    position: absolute;
    left: 70px; top: 130px;
    width: 240px;
    display: flex; align-items: center; gap: 10px;
    font-family: "Comic Neue", sans-serif;
    font-weight: 700;
    font-size: 40px;
    color: var(--brand-green);
  }
  .brand-dot { width: 14px; height: 14px; border-radius: 50%; background: var(--brand-yellow); flex: none; }
  .divider {
    position: absolute; left: 316px; top: 88px;
    width: 1px; height: 155px; background: var(--divider);
  }
  .contact { position: absolute; left: 343px; top: 94px; }
  .contact__name {
    font-family: "Comic Neue", sans-serif; font-weight: 700;
    font-size: 23px; color: var(--brand-green); line-height: 28px;
  }
  .contact__role {
    font-family: "Comic Neue", sans-serif; font-weight: 700;
    font-size: 15px; color: var(--brand-yellow); line-height: 18px;
  }
  .contact__city { margin-top: 12px; font-size: 13px; color: var(--ink-grey); }
  .contact__list { list-style: none; margin-top: 10px; }
  .contact__item {
    display: flex; align-items: center; gap: 9px;
    font-size: 13px; color: var(--ink-grey); line-height: 19px;
  }
  .contact__item svg { width: 13px; height: 13px; flex: none; }
  .front-wave { position: absolute; left: 0; bottom: 0; width: 600px; height: 70px; }

  /* back */
  .city-river {
    position: absolute; inset: 0;
    background:
      radial-gradient(circle at 33% 22%, rgba(255,255,240,0.95) 0, rgba(255,255,240,0.4) 60px, transparent 150px),
      linear-gradient(180deg, var(--sky-top) 0%, var(--sky-mid) 42%, #8a9a8c 62%, var(--water) 78%, #2c4566 100%);
  }
  .back-brand {
    position: absolute; left: 0; right: 0; top: 140px;
    display: flex; justify-content: center; align-items: center; gap: 12px;
    font-family: "Comic Neue", sans-serif; font-weight: 700;
    font-size: 58px; color: var(--white);
  }
  .back-brand .brand-dot { width: 18px; height: 18px; background: var(--white); }
  .tagline {
    position: absolute; left: 0; right: 0; top: 296px;
    display: flex; justify-content: center; align-items: center; gap: 6px;
    font-style: italic; font-weight: 700; font-size: 15px; color: var(--white);
  }
  .tagline__rule { width: 44px; height: 1px; background: rgba(255,255,255,0.8); }
</style>
</head>
<body>

<section class="card card--front" aria-label="Business card front">
  <div class="brand-name"><span class="brand-dot"></span>Kelvoria</div>
  <div class="divider"></div>
  <div class="contact">
    <div class="contact__name">Tomas Bilbrea</div>
    <div class="contact__role">Managing Director</div>
    <div class="contact__city">Melbourne, Australia</div>
    <ul class="contact__list">
      <li class="contact__item">
        <svg viewBox="0 0 16 16"><path fill="#16724a" d="M3.5 1.5l2.5 0 1 3.5-1.8 1.2a9 9 0 0 0 4.6 4.6L11 9l3.5 1v2.5c0 1-1 2-2 2C6.5 14.5 1.5 9.5 1.5 3.5c0-1 1-2 2-2z"/></svg>
        +61 491058264
      </li>
      <li class="contact__item">
        <svg viewBox="0 0 16 16"><rect x="1" y="3" width="14" height="10" rx="1" fill="#16724a"/><path d="M1.5 4l6.5 5 6.5-5" stroke="#f7f7f7" stroke-width="1.4" fill="none"/></svg>
        tomas@kelvarin.com.au
      </li>
      <li class="contact__item">
        <svg viewBox="0 0 16 16"><circle cx="8" cy="8" r="7" fill="#16724a"/><path d="M1 8h14M8 1c-3 3-3 11 0 14M8 1c3 3 3 11 0 14" stroke="#f7f7f7" stroke-width="1" fill="none"/></svg>
        www.kelvoria.com.au
      </li>
    </ul>
  </div>
  <svg class="front-wave" viewBox="0 0 600 70" preserveAspectRatio="none" aria-hidden="true">
    <path d="M0 12 C160 38 380 44 600 24 L600 70 L0 70 Z" fill="var(--brand-yellow)"/>
    <path d="M0 24 C170 48 390 52 600 30 L600 70 L0 70 Z" fill="var(--white)"/>
    <path d="M0 30 C170 54 390 58 600 34 L600 70 L0 70 Z" fill="var(--brand-green)"/>
  </svg>
</section>

<section class="card card--back" aria-label="Business card back">
  <div class="city-river" role="img" aria-label="Photograph of the Yarra River in Melbourne with city skyline and sunlight"></div>
  <div class="back-brand"><span class="brand-dot"></span>Kelvoria</div>
  <div class="tagline"><span class="tagline__rule"></span>Hacemos más por ti!<span class="tagline__rule"></span></div>
</section>

</body>
</html>
```